Vensol Holdings Web Design

Vensol Holdings Limited Shenzhen

This project is a 10 page launch website.
Our client is seeking a contemporary homepage design for a Holdings company. Once we are happy with the homepage design and select designer we will request a secondary page design.

Please see attached company LOGO for an idea of style, it incorporates the traditional Chinese furniture lattice work. The Corvel crest website is one of our clients favorite so we would like to see a similar homepage design to this website.

Use the websites below for reference purpose. The first two are Chinese and the second two are international. We would like to see elements of both but more focus on international design.

http://www.evergrande.com/http://www.taurenfield.com/pub/default.aspx http://www.corvelcrest.com/zh/maldives_lorinhaven/
http://www.quelba-studio.com
http://media-cache-ex0.snapvalu.com/originals/71/a3/19/71a319c5b2d04e8f6a17c3b9e5d0f4a1.jpg

Company Background
VENSOL HOLDINGS, located in Qianhai, China, is a new real-estate project operator, structuring urban-rural real-estate investment and development, and industrial fund investment. The company also invests in supply chain management and supporting infrastructures. To create new spaces and livable cities Vensol Holdings develop win-win strategic partnerships with a number of institutions. Currently cooperating with Tianjing North Lumore, China urban and rural integrated demonstration.

Target Market(s)

B2B property investment. Target market customers are senior level management/decision makers of large corporations. Focusing geographically on the domestic market first and expanding internationally in 2nd and 3rd years.

Industry/Entity Type

Investment

Requirements
Must have
• Since this is a new company, we would like to the website representing growth and power, E.g. like a growing tree.
Should not have
• Low-level vectors such as curency symbols, American dollar.

```html
<!DOCTYPE html>
<html lang="en">
<head>
<meta charset="utf-8">
<title>Vensol Holdings</title>
<link rel="stylesheet" href="https://fonts.googleapis.com/css2?family=Heebo:wght@300;400;500;700&display=swap">
<style>
:root{
  --purple:#8c5a94;
  --purple-dark:#6d4174;
  --purple-soft:rgba(150,96,160,.88);
  --ink:#2b2b2b;
  --text:#3a3a3a;
  --muted:#8a8a8a;
  --rule:#e2e2e2;
  --nav-dark:#262626;
  --nav-mid:#3a3a3a;
  --footer:#262626;
  --white:#ffffff;
}
*{box-sizing:border-box;margin:0;padding:0}
html,body{width:1200px;height:2343px;overflow:hidden;background:var(--white)}
body{position:relative;font-family:"Heebo",Arial,sans-serif;color:var(--text)}
.abs{position:absolute}

/* hero */
.hero{left:0;top:0;width:1200px;height:668px;overflow:hidden;
  background:radial-gradient(ellipse at 50% 30%,#bdbdbd 0%,#8e8e8e 45%,#5a5a5a 80%,#3f3f3f 100%)}
.hero-scene{left:0;top:0;width:1200px;height:665px;
  background:linear-gradient(180deg,rgba(255,255,255,.35) 0%,rgba(255,255,255,0) 30%,rgba(0,0,0,.15) 70%,rgba(0,0,0,.35) 100%)}
.hero-edge{left:0;top:663px;width:1200px;height:5px;background:var(--purple)}
.brand{left:450px;top:22px;width:300px;text-align:center}
.brand-mark{display:block;margin:0 auto 8px;width:62px;height:62px;border-radius:50%;background:#b8902f}
.brand-name{font-size:17px;font-weight:500;color:#b8902f;letter-spacing:.5px}
.lang{left:1003px;top:20px;width:82px;height:25px;border-radius:3px;
  background:linear-gradient(#9a67a2,var(--purple-dark));color:var(--white);font-size:12px;
  line-height:25px;padding-left:10px}
.lang svg{position:absolute;right:9px;top:10px}
.note{background:radial-gradient(ellipse at center,rgba(255,255,255,.05),rgba(255,255,255,0) 70%)}
.note-hire{left:1015px;top:60px;width:60px;height:70px}
.note-know{left:632px;top:545px;width:150px;height:40px}
.nav{left:115px;top:154px;width:970px;height:40px;display:flex;
  background:linear-gradient(var(--nav-mid),var(--nav-dark));border-radius:2px;box-shadow:0 2px 6px rgba(0,0,0,.4)}
.nav a{flex:auto;color:var(--white);font-size:12.5px;font-weight:500;text-decoration:none;
  line-height:40px;text-align:center;border-right:1px solid #1a1a1a;border-left:1px solid #474747}
.nav a.is-active{background:linear-gradient(#a472ac,var(--purple-dark));flex:0 0 80px}
.hero-title{left:0;top:250px;width:1200px;text-align:center;font-size:56px;font-weight:300;color:var(--white);letter-spacing:-.5px}
.team{left:364px;top:334px;display:flex;gap:20px}
.team span{display:block;width:99px;height:99px;border-radius:50%;border:4px solid var(--white);
  background:linear-gradient(160deg,#f3efec,#b6aaa3 55%,#24324c)}
.hero-text{left:170px;top:447px;width:860px;text-align:center;color:var(--white);font-size:18px;line-height:25px;font-weight:400}
.hero-btn{left:543px;top:519px;width:112px;height:38px;border-radius:4px;
  background:linear-gradient(#a875b0,var(--purple-dark));color:var(--white);font-weight:700;font-size:15px;
  text-align:center;line-height:38px;box-shadow:0 2px 4px rgba(0,0,0,.4)}
.dots{left:560px;top:625px;display:flex;gap:6px}
.dots i{width:15px;height:15px;border-radius:50%;background:#e4e4e4;display:block}
.dots i.on{background:var(--purple)}

/* welcome */
.welcome{left:0;top:728px;width:1200px;text-align:center}
.welcome h2{font-size:30px;font-weight:300;color:var(--ink)}
.welcome h1{font-size:50px;font-weight:300;color:var(--purple);line-height:56px}
.welcome-copy{left:152px;top:838px;width:896px;text-align:center;font-size:13px;line-height:19px;color:#444}
.welcome-copy p+p{margin-top:16px}

/* gallery */
.gallery{left:0;top:1057px;width:1200px;height:594px;display:grid;
  grid-template-columns:repeat(4,1fr);grid-template-rows:repeat(3,1fr);gap:5px}
.tile{position:relative;overflow:hidden}
.tile.warm{background:linear-gradient(160deg,#d9b77a,#7a6a58 60%,#3f3a36)}
.tile.dusk{background:linear-gradient(180deg,#6e76b4,#2d2d5a 70%,#141420)}
.tile.sunset{background:linear-gradient(180deg,#f0a064,#6a3a30 65%,#1a1212)}
.tile.sky{background:linear-gradient(180deg,#3b74c7,#9cb3cf 60%,#6e6455)}
.tile.site{background:linear-gradient(180deg,#cfd6dc,#a08d72 55%,#5d5347)}
.tile.feature{background:linear-gradient(160deg,#c9bca5,#8a7d6b)}
.feature-overlay{position:absolute;inset:0;background:var(--purple-soft);color:var(--white);text-align:center}
.feature-overlay h3{font-size:24px;font-weight:400;margin-top:26px}
.feature-icons{display:flex;justify-content:center;gap:6px;margin-top:14px}
.feature-icons span{width:30px;height:30px;background:var(--white);border-radius:2px;display:flex;align-items:center;justify-content:center}
.feature-overlay p{font-size:13px;font-weight:700;line-height:16px;margin:22px 14px 0}

/* news & services */
.col-title{font-size:36px;font-weight:300;color:var(--purple)}
.news{left:115px;top:1722px;width:600px}
.news ul{list-style:none;margin-top:18px}
.news li{position:relative;padding-left:31px;font-size:13.5px;line-height:17px;color:#444;height:49px}
.news li svg{position:absolute;left:0;top:2px}
.divider{left:763px;top:1719px;width:1px;height:295px;background:var(--rule)}
.services{left:818px;top:1722px;width:300px}
.services ol{list-style:none;margin-top:16px}
.services li{display:flex;align-items:center;font-size:13.5px;color:#444;height:26.7px}
.services li b{width:17px;height:17px;border-radius:50%;background:var(--purple);color:var(--white);
  font-size:10px;font-weight:500;text-align:center;line-height:17px;margin-right:12px}
.services li:first-child b{background:#1e1e1e}

/* tweet */
.rule{left:115px;width:970px;height:1px;background:var(--rule)}
.tweet{left:155px;top:2094px;width:930px;font-size:11.5px;color:#555}
.tweet i{position:absolute;left:-34px;top:-2px;width:20px;height:20px;border-radius:50%;background:var(--purple)}
.tweet b{color:var(--purple)}
.tweet em{color:var(--purple);font-weight:700}

/* contacts */
.contact{top:2180px;display:flex;align-items:center;gap:14px;font-size:20px;color:var(--ink)}
.contact .icon{width:35px;height:35px;border-radius:50%;background:var(--purple);display:flex;align-items:center;justify-content:center}
.contact.phone{left:118px;font-size:24px}
.contact.mail{left:415px}
.contact.support{left:773px}

/* footer */
.footer{left:0;top:2263px;width:1200px;height:80px;background:var(--footer)}
.foot-nav{left:115px;top:2290px;display:flex;gap:23px}
.foot-nav a{color:var(--white);font-size:10.5px;font-weight:500;text-decoration:none}
.foot-nav a.is-active{color:var(--purple)}
.copyright{left:115px;top:2313px;font-size:8.5px;color:#8a8a8a;letter-spacing:.2px}
.stay{left:890px;top:2290px;color:var(--white);font-size:13px;font-weight:500;letter-spacing:.6px}
.social{left:1000px;top:2284px;display:flex;gap:6px}
.social span{width:27px;height:27px;border-radius:50%;background:var(--purple)}
.social span:first-child{background:var(--white)}
</style>
</head>
<body>

<div class="abs hero">
  <div class="abs hero-scene" role="img" aria-label="Blurred black and white aerial view of a city skyline"></div>
  <div class="abs hero-edge"></div>
</div>

<div class="abs brand">
  <span class="brand-mark"></span>
  <span class="brand-name">Vensol Holdings</span>
</div>

<div class="abs lang">English
  <svg width="9" height="6" viewBox="0 0 9 6"><path d="M0 0h9L4.5 6z" fill="#fff"/></svg>
</div>
<div class="abs note note-hire" role="img" aria-label="Hand-lettered 'Hire Us' note with curved arrow"></div>

<nav class="abs nav">
  <a class="is-active" href="#">Home</a>
  <a href="#">About Us</a>
  <a href="#">Incorporate</a>
  <a href="#">Trademarks</a>
  <a href="#">Partners</a>
  <a href="#">Services</a>
  <a href="#">Registered Office</a>
  <a href="#">Special Structures</a>
  <a href="#">Blog</a>
  <a href="#">Contact Us</a>
</nav>

<div class="abs hero-title">Lorem ipsum dolor sit amet</div>
<div class="abs team">
  <span role="img" aria-label="Portrait of team member"></span>
  <span role="img" aria-label="Portrait of team member"></span>
  <span role="img" aria-label="Portrait of team member in hard hat"></span>
  <span role="img" aria-label="Portrait of team member"></span>
</div>
<p class="abs hero-text">Lorem ipsum dolor sit amet, consectetur adipiscing elit. Nulla lobortis consequat mauris, eget eleifend nunc viverra viverra. Ut ac risus odio. Aliquam pretium purus sed nulla</p>
<div class="abs hero-btn">Click Here</div>
<div class="abs note note-know" role="img" aria-label="Hand-lettered 'Know More' note with arrow"></div>
<div class="abs dots"><i class="on"></i><i></i><i></i><i></i></div>

<section class="abs welcome">
  <h2>Welcome to</h2>
  <h1>Vensol Holdings</h1>
</section>
<div class="abs welcome-copy">
  <p>Lorem ipsum dolor sit amet, consectetur adipiscing elit. Nulla lobortis consequat mauris, eget eleifend nunc viverra viverra. Ut ac risus odio. Aliquam pretium purus sed nulla feugiat blandit. Cras vel libero ut lacus eleifend tempor.</p>
  <p>Phasellus eleifend, magna non tincidunt accumsan, justo arcu cursus ipsum, non porttitor sapien quam vel magna. Maecenas elit nisl, molestie nec dapibus nec, aliquet a erat. Donec scelerisque lacus a libero suscipit auctor volutpat enim euismod. Mauris porta, lacus ut ullamcorper sodales, mauris tortor feugiat purus, nec aliquam neque purus ac metus. Nunc eleifend leo quis nisl hendrerit ultrices. Suspendisse quis feugiat elit. Fusce vitae dolor ac est tincidunt feugiat. Phasellus volutpat dui in sapien malesuada tempus placerat justo ultricies. Duis mollis ornare risus, ut consectetur mi tincidunt sit amet. Maecenas quis nibh ac orci tempus scelerisque ac et massa.</p>
</div>

<section class="abs gallery">
  <div class="tile warm" role="img" aria-label="Architects reviewing plans on a building site"></div>
  <div class="tile dusk" role="img" aria-label="Silhouettes of engineers and cranes at dusk"></div>
  <div class="tile feature" role="img" aria-label="Engineers in hard hats on site">
    <div class="feature-overlay">
      <h3>Mauris Tortor</h3>
      <div class="feature-icons">
        <span><svg width="14" height="14" viewBox="0 0 14 14"><path d="M6 8l2-2M5 6L3 8a2 2 0 003 3l2-2M9 8l2-2a2 2 0 00-3-3L6 5" stroke="#333" stroke-width="1.6" fill="none"/></svg></span>
        <span><svg width="14" height="14" viewBox="0 0 14 14"><circle cx="6" cy="6" r="4" stroke="#333" stroke-width="1.6" fill="none"/><path d="M9 9l4 4" stroke="#333" stroke-width="1.8"/></svg></span>
      </div>
      <p>Mauris porta, lacus ut ullamcorper sodales, mauris tortor feugiat purus, nec</p>
    </div>
  </div>
  <div class="tile site" role="img" aria-label="Workers on timber scaffolding"></div>
  <div class="tile sunset" role="img" aria-label="Excavator silhouette at sunset"></div>
  <div class="tile site" role="img" aria-label="Engineers in front of a house under construction"></div>
  <div class="tile sky" role="img" aria-label="Tower cranes over a construction site"></div>
  <div class="tile warm" role="img" aria-label="Engineers pointing at a building frame"></div>
  <div class="tile sky" role="img" aria-label="Glass office towers and cranes"></div>
  <div class="tile sky" role="img" aria-label="Handshake in front of a crane with hard hat"></div>
  <div class="tile site" role="img" aria-label="Excavator on a city construction site"></div>
  <div class="tile site" role="img" aria-label="Engineers studying plans beside a building"></div>
</section>

<section class="abs news">
  <h2 class="col-title">Latest News</h2>
  <ul>
    <li><svg width="13" height="15" viewBox="0 0 13 15"><rect x="0" y="2" width="13" height="13" fill="#8c5a94"/><rect x="2" y="6" width="9" height="7" fill="#fff"/><path d="M3 0v4M10 0v4" stroke="#8c5a94" stroke-width="2"/></svg>Lorem ipsum dolor sit amet, consectetur adipiscing elit. Nulla lobortis consequat mauris, eget eleifend nunc viverra viverra. Ut ac risus odio....</li>
    <li><svg width="13" height="15" viewBox="0 0 13 15"><rect x="0" y="2" width="13" height="13" fill="#8c5a94"/><rect x="2" y="6" width="9" height="7" fill="#fff"/><path d="M3 0v4M10 0v4" stroke="#8c5a94" stroke-width="2"/></svg>Aliquam pretium purus sed nulla feugiat blandit. Cras vel libero ut lacus eleifend tempor. Phasellus eleifend, magna non tincidunt accumsan...</li>
    <li><svg width="13" height="15" viewBox="0 0 13 15"><rect x="0" y="2" width="13" height="13" fill="#8c5a94"/><rect x="2" y="6" width="9" height="7" fill="#fff"/><path d="M3 0v4M10 0v4" stroke="#8c5a94" stroke-width="2"/></svg>Lorem ipsum dolor sit amet, consectetur adipiscing elit. Nulla lobortis consequat mauris, eget eleifend nunc viverra viverra. Ut ac risus odio....</li>
    <li><svg width="13" height="15" viewBox="0 0 13 15"><rect x="0" y="2" width="13" height="13" fill="#8c5a94"/><rect x="2" y="6" width="9" height="7" fill="#fff"/><path d="M3 0v4M10 0v4" stroke="#8c5a94" stroke-width="2"/></svg>Aliquam pretium purus sed nulla feugiat blandit. Cras vel libero ut lacus eleifend tempor. Phasellus eleifend, magna non tincidunt accumsan...</li>
    <li><svg width="13" height="15" viewBox="0 0 13 15"><rect x="0" y="2" width="13" height="13" fill="#8c5a94"/><rect x="2" y="6" width="9" height="7" fill="#fff"/><path d="M3 0v4M10 0v4" stroke="#8c5a94" stroke-width="2"/></svg>Lorem ipsum dolor sit amet, consectetur adipiscing elit. Nulla lobortis consequat mauris, eget eleifend nunc viverra viverra. Ut ac risus odio....</li>
  </ul>
</section>

<div class="abs divider"></div>

<section class="abs services">
  <h2 class="col-title">Our Services</h2>
  <ol>
    <li><b>1</b>Lorem ipsum dolor sit amet,</li>
    <li><b>2</b>Consectetur adipiscing elit. Nulla</li>
    <li><b>3</b>Lobortis consequat mauris, eget</li>
    <li><b>4</b>Eleifend nunc viverra viverra. Ut ac</li>
    <li><b>5</b>Risus odioAliquam pretium purus</li>
    <li><b>6</b>Sed nulla feugiat blandit. Cras vel</li>
    <li><b>7</b>Libero ut lacus eleifend tempor.</li>
    <li><b>8</b>Phasellus eleifend, magna non</li>
    <li><b>9</b>Tincidunt accumsan</li>
  </ol>
</section>

<div class="abs rule" style="top:2069px"></div>
<p class="abs tweet"><i></i><b>@Lorem ipsum</b> dolor sit amet, consectetur adipiscing elit. Nulla lobortis consequat mauris, eget eleifend nunc viverra viverra. <em>http://acrisusodio.com</em></p>
<div class="abs rule" style="top:2138px"></div>

<div class="abs contact phone">
  <span class="icon"><svg width="16" height="16" viewBox="0 0 16 16"><path d="M3 1l3 3-2 2c1 2 3 4 5 5l2-2 3 3-2 3C6 14 1 9 1 3z" fill="#fff"/></svg></span>
  0000 0000 000
</div>
<div class="abs contact mail">
  <span class="icon"><svg width="16" height="12" viewBox="0 0 16 12"><rect width="16" height="12" rx="1" fill="#fff"/><path d="M0 1l8 6 8-6" stroke="#8c5a94" stroke-width="1.4" fill="none"/></svg></span>
  support@vensolholdings.com
</div>
<div class="abs contact support">
  <span class="icon"><svg width="18" height="16" viewBox="0 0 18 16"><path d="M2 9a7 7 0 0114 0" stroke="#fff" stroke-width="2" fill="none"/><rect x="1" y="8" width="4" height="6" rx="1" fill="#fff"/><rect x="13" y="8" width="4" height="6" rx="1" fill="#fff"/></svg></span>
  support@vensolholdings.com
</div>

<footer class="abs footer"></footer>
<nav class="abs foot-nav">
  <a class="is-active" href="#">Home</a>
  <a href="#">About Us</a>
  <a href="#">Incorporate</a>
  <a href="#">Trademarks</a>
  <a href="#">Partners</a>
  <a href="#">Services</a>
  <a href="#">Registered Office</a>
  <a href="#">Special Structures</a>
  <a href="#">Blog</a>
  <a href="#">Contact Us</a>
</nav>
<p class="abs copyright">COPYRIGHT © 2013 Vensol Holdings Limited. &nbsp;TERMS OF USE | PRIVACY POLICY</p>
<div class="abs stay">STAY WITH US</div>
<div class="abs social"><span></span><span></span><span></span></div>

</body>
</html>
```